business card for horse saddlery

after a new business card for our saddlery, i will add 2 logos we have previously used and they can be used (or not) . Any images can be used from our website also at www.harrowfields.net.au, I have also added our brand logo, which may be good to incorporate on back ? we have over 15, 000 items online, ship Australia Wide.

Target Market(s)

horse owners

Industry/Entity Type

Retail - Equestrian

Contact Information for Business Card

Harrowfield Horse Supplies, 1300 48 62 90, www.harrowfields.net.au, 27 Lindqvist Rd Marrowbank Q 4587

Requirements
Must have
• trailgem is our brand so trailgem logo on back as 'distributers of', easy to read
Nice to have
• professional but fun
Should not have
• double sided (description wont save double sided)

```html
<!DOCTYPE html>
<html lang="en">
<head>
<meta charset="utf-8">
<title>Harrowfield Horse Supplies – Business Card</title>
<link rel="stylesheet" href="https://fonts.googleapis.com/css2?family=Open+Sans:wght@400;600&display=swap">
<style>
  :root {
    --backdrop: #232323;
    --navy: #2a3f7c;
    --gold: #f5b121;
    --white: #ffffff;
    --ink: #1a1a1a;
    --icon-blue: #3a7bd5;
    --rule-grey: #9a9a9a;
    --photo-dark: #060606;
    --photo-light: #cfcfcf;
  }
  * { margin: 0; padding: 0; box-sizing: border-box; }
  html, body {
    width: 1200px; height: 780px; overflow: hidden;
    background: var(--backdrop);
    font-family: "Open Sans", sans-serif;
  }
  .card-set {
    position: absolute; inset: 0;
    display: flex; align-items: center; justify-content: center; gap: 40px;
  }
  .card {
    position: relative; width: 540px; height: 310px; overflow: hidden;
    box-shadow: 0 10px 30px rgba(0,0,0,.5);
  }
  /* Front */
  .card--front { background: var(--navy); }
  .front-brand {
    position: absolute; left: 90px; top: 110px;
    display: flex; align-items: center; gap: 18px;
  }
  .brand-disc {
    width: 86px; height: 86px; border-radius: 50%; background: var(--gold); flex: none;
  }
  .front-brand .brand-name {
    color: var(--white); font-weight: 600; font-size: 30px; line-height: 1.1; width: 250px;
  }
  /* Back */
  .card--back { background: var(--white); }
  .back-art { position: absolute; inset: 0; }
  .back-brand {
    position: absolute; left: 30px; top: 40px;
    display: flex; align-items: center; gap: 12px;
  }
  .back-brand .brand-disc { width: 56px; height: 56px; }
  .back-brand .brand-name {
    color: var(--navy); font-weight: 600; font-size: 21px; line-height: 1.1; width: 170px;
  }
  .partners {
    position: absolute; left: 238px; top: 22px; width: 90px;
    display: flex; flex-direction: column; align-items: center; gap: 14px;
  }
  .partner-badge { width: 54px; height: 34px; border-radius: 6px; background: var(--icon-blue); opacity: .85; }
  .distributor { display: flex; flex-direction: column; align-items: center; gap: 4px; }
  .distributor-mark { width: 26px; height: 26px; background: var(--navy); }
  .distributor-name { color: var(--navy); font-size: 14px; font-weight: 600; letter-spacing: .5px; }
  .contact {
    position: absolute; left: 30px; top: 160px; color: var(--ink);
  }
  .contact .address { font-size: 13px; line-height: 1.35; margin-bottom: 10px; }
  .contact-row { display: flex; align-items: center; gap: 8px; }
  .contact-row .icon { width: 16px; height: 16px; flex: none; }
  .contact .phone { font-size: 22px; font-weight: 600; letter-spacing: .5px; }
  .contact .web { font-size: 13px; letter-spacing: .3px; margin-top: 4px; }
</style>
</head>
<body>
<main class="card-set">
  <section class="card card--front" aria-label="Card front">
    <div class="front-brand">
      <span class="brand-disc"></span>
      <span class="brand-name">Harrowfield Horse Supplies</span>
    </div>
  </section>

  <section class="card card--back" aria-label="Card back">
    <svg class="back-art" viewBox="0 0 540 310" width="540" height="310" aria-hidden="true">
      <path d="M296 0 C350 80 388 200 408 310 L440 310 C420 200 382 80 328 0 Z" fill="var(--gold)"/>
      <path d="M316 0 C368 80 404 200 424 310 L432 310 C412 200 376 80 324 0 Z" fill="var(--rule-grey)"/>
    </svg>
    <svg class="back-art" viewBox="0 0 540 310" width="540" height="310" role="img" aria-label="Photograph of a grey horse wearing a leather halter against a black background">
      <defs>
        <linearGradient id="photoTone" x1="0" y1="0" x2="0.4" y2="1">
          <stop offset="0" stop-color="var(--photo-dark)"/>
          <stop offset="0.45" stop-color="#3a3a3a"/>
          <stop offset="1" stop-color="var(--photo-light)"/>
        </linearGradient>
      </defs>
      <path d="M324 0 C376 80 412 200 432 310 L540 310 L540 0 Z" fill="url(#photoTone)"/>
    </svg>

    <div class="back-brand">
      <span class="brand-disc"></span>
      <span class="brand-name">Harrowfield Horse Supplies</span>
    </div>

    <div class="partners">
      <span class="partner-badge" aria-label="harrowfields"></span>
      <div class="distributor">
        <span class="distributor-mark"></span>
        <span class="distributor-name">trailgem</span>
      </div>
    </div>

    <div class="contact">
      <p class="address">27 Lindqvist Rd<br>Marrowbank Q 4587</p>
      <div class="contact-row">
        <svg class="icon" viewBox="0 0 16 16" aria-hidden="true"><circle cx="8" cy="8" r="8" fill="var(--icon-blue)"/><path d="M5.5 4.5 L7 4.5 L7.6 6.4 L6.8 7.1 C7.3 8.2 7.9 8.8 9 9.3 L9.7 8.5 L11.5 9.1 L11.5 10.6 C8 11 5 8 5.5 4.5 Z" fill="var(--white)"/></svg>
        <span class="phone">1300 48 62 90</span>
      </div>
      <div class="contact-row">
        <svg class="icon" viewBox="0 0 16 16" aria-hidden="true"><circle cx="8" cy="8" r="8" fill="var(--icon-blue)"/><circle cx="8" cy="8" r="4.5" fill="none" stroke="var(--white)" stroke-width="1.2"/><path d="M3.5 8 H12.5 M8 3.5 C6 6 6 10 8 12.5 M8 3.5 C10 6 10 10 8 12.5" fill="none" stroke="var(--white)" stroke-width="1"/></svg>
        <span class="web">www.harrowfields.net.au</span>
      </div>
    </div>
  </section>
</main>
</body>
</html>
```